Lumo Medical Aesthetics - Service Flyer

We are looking to have a friend-fold flyer designed that outlines all of the services offered. I am able to provide pricing on all products and outline of services.

We have had a flyer made in the past and the colours were black and white to go with the logo and keep it simple. We would prefer to keep these colours, but are open to adding in a couple of extra complimentary colours which would match our clinic. I have attached the original flyer that was created as well as our logo.

Target Market(s)

Women aged 25-65

Requirements
Must have
• Our website is www.lumoclinicra.example
• 555-284-7162
• Facebook: lumoclinicra
• Instagram @lumoclinicra
• Services to be included are:
• Some pricing has not been listed, but will update shortly
• Velquin $8/unit
• Renza $10/unit
• Dermal Fillers
• (Cheeks, lips, jawline, chin, temples, under eyes, smile lines, smokers lines)
• 1ml syringe $475
• Mini Lip Plump $250
• Non-Surgical Face Lift $1100
• (Choice of 3 areas, eg. lips, jaw contouring, cheeks)
• Facial Treatments:
• Personalized Facial $85
• Organic Facial -$100
• Deep Cleansing / Acne Facial - $120
• Gel Peel (20% Glycolic/10% Lactic/3.2pH) - $75
• Dermaplaning $120
• Microdermabrasion $120
• Microneedling $250
• Microneedling (package of 3) $600
• Platelet-Rich Plasma (PRP) Facial $400
• Platinum Facial (Dermaplaning + Microneedling) $350
• LED Light Therapy $45
• High Frequency $45
• Skin Consultation (Free)
• Permanent Make-Up:
• Microblading $350
• Microblading Touch-Up $50
• Lashline Enhancement - Top Lashline $300
• Lashline Enhancement - Bottom Lashline $350
• Touch-Up Top/Bottom Lashline $50
• Lip Blush $450
• Lip Blush Touch-up $50
• Tattoo Removal $200 (per session)
• Cosmetic Treatments:
• Classic Eyelash Extensions $99
• Classic Fill $45
• Hybrid Eyelash Extensions $120
• Hybrid Fill $55
• Eyelash Lift & Tint $75
• Teeth Whitening $125
• Organic Teeth Whitening $150
• Medical Aesthetics Treatments:
• Laser Hair Removal $35 and up (per session)
• (Consultation and patch test required for all clients)
• Microneedling for Stretch Marks and Scars - $250 +
• Platelet-Rich Plasma (PRP) Hair Restoration - $500
• Scalp Micropigmentation - $500 and up
• The brivolux / laser hair removal write-up should be replaced with the following:
• We believe in providing only the best for our clients. We specialize in a number of Medical Aesthetics Treatments to address common skin and anti-aging concerns among our clients. All of our treatments are non-invasive, highly effective and affordable. Our services are performed by certified professionals, using clinically proven equipment and products approved and certified through Health Canada.
• We take pride in the high calibre experience we offer our clients and believe that choosing the appropriate certified professional that can deliver the results you desire, is of primary importance. Lumo employs highly qualified professionals, operating under Dr. Malcolm Dunstan, Board Certified Plastic Surgeon acting as the Medical Director, as well as partners of the Tandem Medical team.

```html
<!DOCTYPE html>
<html lang="en">
<head>
<meta charset="utf-8">
<title>Lumo Medical Aesthetics – Service Flyer</title>
<link href="https://fonts.googleapis.com/css2?family=Oswald:wght@500;600&family=Open+Sans:wght@400;600;700&display=swap" rel="stylesheet">
<style>
  :root{
    --canvas:#ecebe9;
    --paper:#ffffff;
    --blush:#c8a197;
    --blush-soft:#e6cfc8;
    --charcoal:#5a5a5c;
    --charcoal-deep:#4a4a4c;
    --ink:#4f4f52;
    --ink-soft:#7a7a7d;
    --rule:#b9b9bb;
  }
  *{box-sizing:border-box;margin:0;padding:0}
  html,body{width:1200px;height:2402px;overflow:hidden;background:var(--canvas)}
  body{font-family:"Open Sans",Arial,sans-serif;color:var(--ink);position:relative}
  .spread{position:absolute;left:30px;width:1140px;height:1080px;display:flex;background:var(--paper);box-shadow:0 6px 24px rgba(0,0,0,.12)}
  .spread--outside{top:60px}
  .spread--inside{top:1242px}
  .panel{position:relative;width:380px;height:100%;overflow:hidden;display:flex;flex-direction:column}
  .panel + .panel{border-left:1px solid #e4e4e4}
  .panel--dark{background:var(--charcoal);color:#f2f2f2}
  .photo{position:relative;flex:none}
  .photo__fill{position:absolute;inset:0}
  .band{flex:none;height:46px;background:var(--blush);display:flex;align-items:center;justify-content:center;color:var(--paper);font-size:17px;font-weight:600;letter-spacing:.3px;margin-top:auto}
  .band--light{background:var(--blush-soft);color:var(--ink)}
  .brand{display:flex;align-items:center;gap:12px;font-family:"Open Sans",Arial,sans-serif;font-weight:400;color:var(--charcoal-deep);letter-spacing:2px;text-transform:uppercase}
  .brand__mark{width:16px;height:16px;background:var(--charcoal-deep);flex:none}
  .brand--light{color:var(--paper)}
  .brand--light .brand__mark{background:var(--paper)}
  .heading{font-family:"Oswald",Arial,sans-serif;font-weight:600;text-transform:uppercase;letter-spacing:.5px}
  .body-copy{font-size:14px;line-height:1.65}
  .body-copy p + p{margin-top:14px}
  .curve{position:absolute;left:0;width:100%;display:block}

  /* outside: about panel */
  .about .photo{height:300px}
  .about__text{padding:28px 32px}
  .about__title{font-size:20px;color:var(--charcoal-deep);margin-bottom:16px}

  /* outside: contact panel */
  .contact{padding:0}
  .contact__top{height:280px;background:var(--paper);position:relative}
  .contact__badge{position:absolute;left:50%;top:50px;transform:translateX(-50%);width:150px;height:150px;border-radius:50%;border:4px solid var(--blush);background:radial-gradient(circle at 45% 45%,#f4f6f2,#d8e3d4)}
  .contact__inner{padding:26px 34px;text-align:center}
  .contact__title{font-size:22px;color:var(--paper);margin-bottom:18px}
  .contact__people{margin-top:28px;font-size:14px;line-height:1.8}
  .contact__more{margin-top:26px;font-size:19px}
  .contact__web{display:flex;align-items:center;justify-content:center;gap:8px;font-size:16px;margin-top:6px}
  .contact__social{margin-top:14px;font-size:14px;line-height:1.8}

  /* outside: cover */
  .cover__head{height:190px;display:flex;align-items:center;justify-content:center;position:relative;z-index:2}
  .cover__head .brand{font-size:26px}
  .cover .photo{height:560px;margin-top:-40px}
  .cover__tagline{font-size:34px;line-height:1.2;color:var(--charcoal-deep);text-align:center;padding:30px 28px 0}
  .cover__web{margin-top:auto;margin-bottom:34px;text-align:center;font-size:20px;font-weight:700;color:var(--blush)}

  /* inside */
  .inside-photo{height:300px}
  .grey-bar{height:22px;background:var(--charcoal);flex:none}
  .prices{padding:22px 30px 0;font-size:13.5px}
  .prices--dark{padding-top:10px}
  .price-group + .price-group{margin-top:18px}
  .price-group__title{font-size:15px;font-weight:700;text-transform:uppercase;letter-spacing:.4px;color:var(--charcoal-deep)}
  .panel--dark .price-group__title{color:var(--paper)}
  .price-group__note{font-size:11.5px;color:var(--ink-soft);margin:2px 0 4px}
  .panel--dark .price-group__note{color:#d5d5d5}
  .price-row{display:flex;align-items:baseline;gap:6px;line-height:1.75}
  .price-row__name{flex:none;max-width:70%}
  .price-row__dots{flex:1;border-bottom:1px dotted var(--rule);transform:translateY(-4px)}
  .panel--dark .price-row__dots{border-color:#9a9a9c}
  .price-row__cost{flex:none;font-weight:600}
  .circle-inset{position:absolute;left:50%;top:130px;transform:translateX(-50%);width:170px;height:170px;border-radius:50%;border:5px solid var(--blush);background:radial-gradient(circle at 40% 45%,#f7e7e3,#d9b3ab);z-index:2}
  .dark-head{padding:40px 30px 26px}
  .dark-head .brand{font-size:24px}
  .dark-web{margin-top:auto;margin-bottom:70px;display:flex;align-items:center;justify-content:center;gap:8px;font-size:17px;font-weight:600}
  .cta{position:absolute;left:0;right:0;bottom:0;height:50px;background:var(--blush);color:var(--paper);display:flex;align-items:center;justify-content:center;font-size:20px;font-weight:600;z-index:3}
</style>
</head>
<body>

<section class="spread spread--outside">
  <!-- about panel -->
  <article class="panel about">
    <div class="photo">
      <div class="photo__fill" role="img" aria-label="Client relaxing during a facial laser treatment" style="background:linear-gradient(135deg,#f1e4df,#d8c0b7 60%,#bfa59b)"></div>
      <svg class="curve" style="bottom:-1px" height="50" viewBox="0 0 380 50" preserveAspectRatio="none"><path d="M0 50 L0 22 Q190 -10 380 30 L380 50 Z" fill="#fff"/><path d="M0 22 Q190 -10 380 30" fill="none" stroke="#c8a197" stroke-width="5"/></svg>
    </div>
    <div class="about__text">
      <h2 class="heading about__title">Lumo Medical Aesthetics</h2>
      <div class="body-copy">
        <p>We believe in providing only the best for our clients. We specialize in a number of Medical Aesthetics Treatments to address common skin and anti-aging concerns among our clients.</p>
        <p>All of our treatments are non-invasive, highly effective and affordable. Our services are performed by certified professionals, using clinically proven equipment and products approved and certified through Health Canada.</p>
      </div>
    </div>
    <div class="band">info@lumoclinicra.example</div>
  </article>

  <!-- contact panel -->
  <article class="panel panel--dark contact">
    <div class="contact__top">
      <div class="contact__badge" role="img" aria-label="Clinic location illustration"></div>
      <svg class="curve" style="bottom:-1px" height="50" viewBox="0 0 380 50" preserveAspectRatio="none"><path d="M0 50 L0 30 Q190 -6 380 22 L380 50 Z" fill="#5a5a5c"/><path d="M0 30 Q190 -6 380 22" fill="none" stroke="#c8a197" stroke-width="5"/></svg>
    </div>
    <div class="contact__inner">
      <h2 class="heading contact__title">We'd love to hear from you!</h2>
      <p class="body-copy">We take pride in the high calibre experience we offer our clients and believe that choosing the appropriate certified professional that can deliver the results you desire, is of primary importance. Lumo employs highly qualified professionals, operating under Dr. Malcolm Dunstan, Board Certified Plastic Surgeon acting as the Medical Director, as well as partners of the Tandem Medical team.</p>
      <div class="contact__people">
        <div>Dana Whitfield 555-284-7163</div>
        <div>Corinne Ashby 555-284-7164</div>
        <div>Priya Lennox 555-284-7162</div>
      </div>
      <p class="contact__more">For more information, visit us at</p>
      <p class="contact__web">
        <svg width="16" height="16" viewBox="0 0 16 16"><circle cx="8" cy="8" r="7" fill="none" stroke="#c8a197" stroke-width="1.6"/><path d="M1 8h14M8 1c-3 4-3 10 0 14M8 1c3 4 3 10 0 14" fill="none" stroke="#c8a197" stroke-width="1.2"/></svg>
        www.lumoclinicra.example
      </p>
      <div class="contact__social">
        <div>Facebook: lumoclinicra</div>
        <div>Instagram: @lumoclinicra</div>
      </div>
    </div>
    <div class="band">www.lumoclinicra.example</div>
  </article>

  <!-- cover -->
  <article class="panel cover">
    <header class="cover__head">
      <div class="brand"><span class="brand__mark"></span>Lumo | Medical Aesthetics</div>
    </header>
    <div class="photo">
      <div class="photo__fill" role="img" aria-label="Woman receiving a facial aesthetics consultation" style="background:linear-gradient(160deg,#f6ece8,#e3cbc3 55%,#c9a99f)"></div>
      <svg class="curve" style="top:-1px" height="60" viewBox="0 0 380 60" preserveAspectRatio="none"><path d="M0 0 L380 0 L380 18 Q190 70 0 30 Z" fill="#fff"/><path d="M0 30 Q190 70 380 18" fill="none" stroke="#c8a197" stroke-width="5"/></svg>
      <svg class="curve" style="bottom:-1px" height="60" viewBox="0 0 380 60" preserveAspectRatio="none"><path d="M0 60 L0 34 Q190 -10 380 26 L380 60 Z" fill="#fff"/><path d="M0 34 Q190 -10 380 26" fill="none" stroke="#c8a197" stroke-width="5"/></svg>
    </div>
    <h1 class="heading cover__tagline">Laser Hair Removal, Renza, Dermal Fillers, Microblading, Lashes and More</h1>
    <p class="cover__web">www.lumoclinicra.example</p>
    <div class="band" style="height:30px;margin-top:0"></div>
  </article>
</section>

<section class="spread spread--inside">
  <!-- injectables & facials -->
  <article class="panel">
    <div class="photo inside-photo">
      <div class="photo__fill" role="img" aria-label="Smooth legs after laser hair removal" style="background:linear-gradient(120deg,#f4ebe6,#dcb8a3 50%,#c59a82)"></div>
    </div>
    <div class="grey-bar"></div>
    <div class="prices">
      <div class="price-group">
        <h3 class="price-group__title">Neuromodulator / Toxin</h3>
        <div class="price-row"><span class="price-row__name">Velquin</span><span class="price-row__dots"></span><span class="price-row__cost">$8/unit</span></div>
        <div class="price-row"><span class="price-row__name">Renza</span><span class="price-row__dots"></span><span class="price-row__cost">$10/unit</span></div>
      </div>
      <div class="price-group">
        <h3 class="price-group__title">Dermal Filler</h3>
        <p class="price-group__note">(Cheeks, lips, jawline, chin, temples, under eyes, smile lines, smokers lines)</p>
        <div class="price-row"><span class="price-row__name">1ml Syringe</span><span class="price-row__dots"></span><span class="price-row__cost">$475</span></div>
        <div class="price-row"><span class="price-row__name">Mini Lip Plump</span><span class="price-row__dots"></span><span class="price-row__cost">$250</span></div>
      </div>
      <div class="price-group">
        <h3 class="price-group__title">Non-Surgical Face Lift</h3>
        <p class="price-group__note">(Choice of 3 areas, eg. lips, jaw contouring, cheeks)</p>
        <div class="price-row"><span class="price-row__name">Face Lift</span><span class="price-row__dots"></span><span class="price-row__cost">$1100</span></div>
      </div>
      <div class="price-group">
        <h3 class="price-group__title">Facial Treatments</h3>
        <div class="price-row"><span class="price-row__name">Personalized Facial</span><span class="price-row__dots"></span><span class="price-row__cost">$85</span></div>
        <div class="price-row"><span class="price-row__name">Organic Facial</span><span class="price-row__dots"></span><span class="price-row__cost">$100</span></div>
        <div class="price-row"><span class="price-row__name">Deep Cleansing / Acne Facial</span><span class="price-row__dots"></span><span class="price-row__cost">$120</span></div>
        <div class="price-row"><span class="price-row__name">Gel Peel (20% Glycolic/10% Lactic/3.2pH)</span><span class="price-row__dots"></span><span class="price-row__cost">$75</span></div>
      </div>
    </div>
  </article>

  <!-- skin treatments -->
  <article class="panel">
    <div class="photo inside-photo">
      <div class="photo__fill" role="img" aria-label="Soft pink spa backdrop" style="background:linear-gradient(135deg,#fbf3f1,#efd9d4 60%,#e3c3bb)"></div>
    </div>
    <div class="circle-inset" role="img" aria-label="Close-up of an eyelash extension treatment"></div>
    <div class="grey-bar"></div>
    <div class="prices">
      <div class="price-group">
        <div class="price-row"><span class="price-row__name">Dermaplaning</span><span class="price-row__dots"></span><span class="price-row__cost">$120</span></div>
        <div class="price-row"><span class="price-row__name">Microdermabrasion</span><span class="price-row__dots"></span><span class="price-row__cost">$120</span></div>
      </div>
      <div class="price-group">
        <h3 class="price-group__title">Microneedling / Collagen Induction Therapy</h3>
        <div class="price-row"><span class="price-row__name">Microneedling</span><span class="price-row__dots"></span><span class="price-row__cost">$250</span></div>
        <div class="price-row"><span class="price-row__name">Microneedling Package of 3</span><span class="price-row__dots"></span><span class="price-row__cost">$600</span></div>
        <div class="price-row"><span class="price-row__name">Platelet-Rich Plasma (PRP) Facial</span><span class="price-row__dots"></span><span class="price-row__cost">$400</span></div>
      </div>
      <div class="price-group">
        <h3 class="price-group__title">Platinum Facial</h3>
        <div class="price-row"><span class="price-row__name">(Dermaplaning + Microneedling)</span><span class="price-row__dots"></span><span class="price-row__cost">$350</span></div>
      </div>
      <div class="price-group">
        <div class="price-row"><span class="price-row__name">LED Light Therapy</span><span class="price-row__dots"></span><span class="price-row__cost">$45</span></div>
        <div class="price-row"><span class="price-row__name">High Frequency</span><span class="price-row__dots"></span><span class="price-row__cost">$45</span></div>
        <div class="price-row"><span class="price-row__name">Skin Consultation</span><span class="price-row__dots"></span><span class="price-row__cost">(Free)</span></div>
      </div>
    </div>
  </article>

  <!-- permanent make-up, cosmetic, medical -->
  <article class="panel panel--dark">
    <header class="dark-head">
      <div class="brand brand--light"><span class="brand__mark"></span>Lumo | Medical Aesthetics</div>
    </header>
    <div class="prices prices--dark">
      <div class="price-group">
        <h3 class="price-group__title">Permanent Make-Up</h3>
        <div class="price-row"><span class="price-row__name">Microblading</span><span class="price-row__dots"></span><span class="price-row__cost">$350</span></div>
        <div class="price-row"><span class="price-row__name">Microblading Touch-Up</span><span class="price-row__dots"></span><span class="price-row__cost">$50</span></div>
        <div class="price-row"><span class="price-row__name">Lashline Enhancement - Top</span><span class="price-row__dots"></span><span class="price-row__cost">$300</span></div>
        <div class="price-row"><span class="price-row__name">Lashline Enhancement - Bottom</span><span class="price-row__dots"></span><span class="price-row__cost">$350</span></div>
        <div class="price-row"><span class="price-row__name">Touch-Up Top/Bottom Lashline</span><span class="price-row__dots"></span><span class="price-row__cost">$50</span></div>
        <div class="price-row"><span class="price-row__name">Lip Blush</span><span class="price-row__dots"></span><span class="price-row__cost">$450</span></div>
        <div class="price-row"><span class="price-row__name">Lip Blush Touch-Up</span><span class="price-row__dots"></span><span class="price-row__cost">$50</span></div>
        <div class="price-row"><span class="price-row__name">Tattoo Removal</span><span class="price-row__dots"></span><span class="price-row__cost">$200 per session</span></div>
      </div>
      <div class="price-group">
        <h3 class="price-group__title">Cosmetic Treatments</h3>
        <div class="price-row"><span class="price-row__name">Classic Eyelash Extensions</span><span class="price-row__dots"></span><span class="price-row__cost">$99</span></div>
        <div class="price-row"><span class="price-row__name">Classic Fill</span><span class="price-row__dots"></span><span class="price-row__cost">$45</span></div>
        <div class="price-row"><span class="price-row__name">Hybrid Eyelash Extensions</span><span class="price-row__dots"></span><span class="price-row__cost">$120</span></div>
        <div class="price-row"><span class="price-row__name">Hybrid Fill</span><span class="price-row__dots"></span><span class="price-row__cost">$55</span></div>
        <div class="price-row"><span class="price-row__name">Eyelash Lift &amp; Tint</span><span class="price-row__dots"></span><span class="price-row__cost">$75</span></div>
        <div class="price-row"><span class="price-row__name">Teeth Whitening</span><span class="price-row__dots"></span><span class="price-row__cost">$125</span></div>
        <div class="price-row"><span class="price-row__name">Organic Teeth Whitening</span><span class="price-row__dots"></span><span class="price-row__cost">$150</span></div>
      </div>
      <div class="price-group">
        <h3 class="price-group__title">Medical Aesthetics Treatments</h3>
        <div class="price-row"><span class="price-row__name">Laser Hair Removal (per session)</span><span class="price-row__dots"></span><span class="price-row__cost">$35 +</span></div>
        <p class="price-group__note">(Consultation and patch test required for all clients)</p>
        <div class="price-row"><span class="price-row__name">Microneedling Stretch Marks/Scars</span><span class="price-row__dots"></span><span class="price-row__cost">$250 +</span></div>
        <div class="price-row"><span class="price-row__name">PRP Hair Restoration</span><span class="price-row__dots"></span><span class="price-row__cost">$500</span></div>
        <div class="price-row"><span class="price-row__name">Scalp Micropigmentation</span><span class="price-row__dots"></span><span class="price-row__cost">$500 +</span></div>
      </div>
    </div>
    <p class="dark-web">
      <svg width="16" height="16" viewBox="0 0 16 16"><circle cx="8" cy="8" r="7" fill="none" stroke="#c8a197" stroke-width="1.6"/><path d="M1 8h14M8 1c-3 4-3 10 0 14M8 1c3 4 3 10 0 14" fill="none" stroke="#c8a197" stroke-width="1.2"/></svg>
      www.lumoclinicra.example
    </p>
  </article>

  <div class="cta">Please get in touch for an informal chat or for a free care assessment.</div>
</section>

</body>
</html>
```